Elegant Business Card for Technology Company

Client is a supplier of innovative industrial communications and automation equipment since 2002. This contest is to gather fresh ideas for a redesign of the existing business card. Client is looking for design that best communicates tagline "Industrial Networking and Computing Specialist".

Design submissions should look modern, clean, elegant and professional. It should not be cluttered. Use white as the primary colour. Orange and black as secondary colour. Refer to jpeg File 1 on the current design.

Fonts used by Client used include Arial Regular, Arial Black, Roboto Regular, Roboto Black and Lato.

The winning design will be sent for offset printing using super white 250gsm artcard paper (open for suggestions).

Target Market(s)

System Engineers, Project Managers, Purchasing Managers from companies providing engineering services for Smart Cities.

Industry/Entity Type

Information Technology

Contact Information for Business Card

Refer to PDF File 3 for Business Card Details. Priority of short contact information would be as follows Name > Job Title > Email > Mobile > Web > Tel > Fax > Business Address >UEN (UEN represents company registration number)

Font styles to use
Sans Serif

Colors
ffffff
f37122
000000
5c5c5c

Requirements
Must have
• Refer to AI File 2 (Company Logo) & PDF File 3 (Information on Namecard)
Should not have
• No QR codes
• No Social Media Icons
• Do not create full Black or Orange colour background

```html
<!DOCTYPE html>
<html lang="en">
<head>
<meta charset="utf-8">
<title>KORA Business Card</title>
<link rel="stylesheet" href="https://fonts.googleapis.com/css2?family=Open+Sans:wght@400;600;700&display=swap">
<style>
  :root {
    --white: #ffffff;
    --orange: #f37122;
    --black: #000000;
    --grey-text: #5c5c5c;
    --backdrop: #8a8a8a;
    --scale: 1.4048;
  }
  * { margin: 0; padding: 0; box-sizing: border-box; }
  html, body {
    width: 1105px;
    height: 1200px;
    overflow: hidden;
    background: var(--backdrop);
    font-family: "Open Sans", Arial, sans-serif;
  }
  .card {
    position: absolute;
    left: 172px;
    width: 760px;
    height: 434px;
    background: var(--white);
    overflow: hidden;
  }
  .card--front { top: 120px; }
  .card--back { top: 646px; }
  .card__face {
    position: absolute;
    left: 0;
    top: 0;
    width: 541px;
    height: 309px;
    transform: scale(var(--scale));
    transform-origin: 0 0;
  }
  .card__shapes {
    position: absolute;
    inset: 0;
    width: 541px;
    height: 309px;
  }
  .holder {
    position: absolute;
    left: 25px;
    top: 20px;
    color: var(--white);
  }
  .holder__name {
    font-size: 20px;
    font-weight: 600;
    line-height: 1.2;
  }
  .holder__title {
    font-size: 14px;
    font-weight: 400;
    line-height: 1.3;
  }
  .address {
    position: absolute;
    left: 28px;
    top: 116px;
    color: var(--white);
    font-size: 13.5px;
    line-height: 19.5px;
    font-style: normal;
  }
  .contacts {
    position: absolute;
    left: 28px;
    top: 185px;
    list-style: none;
    color: var(--white);
    font-size: 13.5px;
    line-height: 20.7px;
  }
  .contacts__item {
    display: flex;
    align-items: center;
    gap: 7px;
  }
  .contacts__icon {
    width: 13px;
    height: 13px;
    flex: none;
  }
  .brand {
    position: absolute;
    display: flex;
    align-items: center;
    gap: 12px;
  }
  .brand--front { left: 294px; top: 115px; gap: 9px; }
  .brand--back { left: 163px; top: 65px; }
  .brand__dot {
    width: 86px;
    height: 86px;
    border-radius: 50%;
    background: var(--orange);
    flex: none;
  }
  .brand--front .brand__dot { width: 72px; height: 72px; }
  .brand__name {
    font-size: 54px;
    font-weight: 700;
    color: var(--black);
    letter-spacing: 1px;
    line-height: 1;
    white-space: nowrap;
  }
  .brand--front .brand__name { font-size: 44px; letter-spacing: 0.5px; }
  .services {
    position: absolute;
    left: 0;
    right: 0;
    top: 211px;
    text-align: center;
    color: var(--grey-text);
    font-size: 14.5px;
    line-height: 19.3px;
    list-style: none;
  }
  .services__sep {
    display: inline-block;
    width: 5px;
    height: 5px;
    margin: 0 4px 2px;
    border-radius: 50%;
    background: var(--orange);
    vertical-align: middle;
  }
</style>
</head>
<body>
  <section class="card card--front" aria-label="Business card front">
    <div class="card__face">
      <svg class="card__shapes" viewBox="0 0 541 309" aria-hidden="true">
        <path d="M0 0 H275 Q232 155 290 309 H0 Z" fill="var(--orange)"/>
        <path d="M275 0 H283 Q240 155 298 309 H290 Q232 155 275 0 Z" fill="var(--black)"/>
      </svg>

      <header class="holder">
        <h1 class="holder__name">Daniel Koh</h1>
        <p class="holder__title">Sales Manager</p>
      </header>

      <address class="address">
        24 Kallang Way Harbour<br>
        Techpark #02-15 (Block B)<br>
        Singapore 349210
      </address>

      <ul class="contacts">
        <li class="contacts__item">
          <svg class="contacts__icon" viewBox="0 0 16 16" aria-hidden="true"><path fill="var(--white)" d="M3.5 1 L6 1 L7 5 L5.2 6.4 Q6.6 9.4 9.6 10.8 L11 9 L15 10 L15 12.5 Q14.5 15 12 15 Q2 13 1 4 Q1 1.5 3.5 1 Z"/></svg>
          <span>+65 6100 2040</span>
        </li>
        <li class="contacts__item">
          <svg class="contacts__icon" viewBox="0 0 16 16" aria-hidden="true"><rect x="4" y="1" width="8" height="14" rx="1.5" fill="var(--white)"/><rect x="5.3" y="3" width="5.4" height="8.5" fill="var(--orange)"/><circle cx="8" cy="13.2" r="0.9" fill="var(--orange)"/></svg>
          <span>+65 9100 2233</span>
        </li>
        <li class="contacts__item">
          <svg class="contacts__icon" viewBox="0 0 16 16" aria-hidden="true"><rect x="4" y="1" width="8" height="4" fill="var(--white)"/><rect x="1" y="6" width="14" height="6" rx="1" fill="var(--white)"/><rect x="4" y="10" width="8" height="5" fill="var(--white)" stroke="var(--orange)" stroke-width="1"/></svg>
          <span>+65 6100 2041</span>
        </li>
        <li class="contacts__item">
          <svg class="contacts__icon" viewBox="0 0 16 16" aria-hidden="true"><rect x="1" y="3" width="14" height="10" fill="var(--white)"/><path d="M1.5 3.5 L8 9 L14.5 3.5" fill="none" stroke="var(--orange)" stroke-width="1.2"/></svg>
          <span>sales@kora.com.sg</span>
        </li>
        <li class="contacts__item">
          <svg class="contacts__icon" viewBox="0 0 16 16" aria-hidden="true"><circle cx="8" cy="8" r="7" fill="var(--white)"/><path d="M5 3 Q7 5 5.5 7 Q8 8 7 11 M10 4 Q9 6 11.5 7 Q12 10 10 12" fill="none" stroke="var(--orange)" stroke-width="1.3"/></svg>
          <span>www.kora.com.sg</span>
        </li>
      </ul>

      <div class="brand brand--front">
        <span class="brand__dot" aria-hidden="true"></span>
        <span class="brand__name">KORA</span>
      </div>
    </div>
  </section>

  <section class="card card--back" aria-label="Business card back">
    <div class="card__face">
      <div class="brand brand--back">
        <span class="brand__dot" aria-hidden="true"></span>
        <span class="brand__name">KORA</span>
      </div>

      <ul class="services">
        <li>Industrial Networking &amp; Computing Specialist</li>
        <li>Industrial Ethernet<span class="services__sep"></span>Wireless<span class="services__sep"></span>Cellular</li>
        <li>Industrial &amp; Embedded Computing<span class="services__sep"></span>Serial<span class="services__sep"></span>Fieldbus Connectivity</li>
        <li>IP Video Surveillance<span class="services__sep"></span>Remote Automation</li>
      </ul>
    </div>
  </section>
</body>
</html>
```